Title: Iron Ledger Sub: She never leaves the harbor - Book cover

I need a complete book cover, front, spine, and back.

Religions Book

This book is more about the Title so it should be strong and serious.

Like the color Deep Red and black, blue. Deep purple
Avoid greens, orange, yellows.

Maybe a picture of a strong hand on the Bible. OR someone yelling.

If any pictures are used they must be 100% royalty free with proof or a buyout of image.

I have attached a couple of designs that the client likes. Just as a reference. The exception they DIDN'T like the pictures in the book cover.

Please ask any questions to clarify.

Please see the file I just uploaded called 'Book Cover samples.png" The clients likes the Title: Salt and Ember" the best. Please create a design something closer to this. The like how the title jumps off the page with a 2D look.

Again the Title must standout, and any use of images must be a secondary to the design.

I am happy with we the designs that have been submitted so far.

I hope this helps you get closer.

Thank you

First of all I want to thank you for all of your designs. At the beginning the client thought he would like a picture that represented the title. But after looking at all of the designs. He has now decided NOT to have any pictures.

Here is what he wants

1. BOLD Font (San Serif only) no fancy versions for the Title "IRON LEDGER" in uppercase. The title font should have some dimension to it to appear 2D or 3D looks. Shiny look. It needs to looks like it jumping off the page.

2. The subtitle right below the title in San Serif font)

3. Background solid color either black, dark red, or dark blue. The background can be slightly textured or gradation fill, etc.

4. The cover must have a strong and bold statement.

Thank you again.

Please use this photo on the back cover.

Thank you

Requirements
Should not have
• A picture that over powers the Title.

```html
<!DOCTYPE html>
<html lang="en">
<head>
<meta charset="UTF-8">
<title>Iron Ledger – Book Cover</title>
<link rel="stylesheet" href="https://fonts.googleapis.com/css2?family=Alike&family=Tinos&family=Oswald:wght@700&family=Montserrat:wght@500&display=swap">
<style>
  :root {
    --ink-black: #000000;
    --cover-red: #ed1c24;
    --brush-blue: #2e3192;
    --title-face: #141414;
    --title-edge: #4a0a0e;
    --title-depth: #2a0407;
    --shine-top: #f2f2f2;
    --shine-mid: #8a8a8a;
    --shine-low: #1c1c1c;
    --sub-ink: #2a0b0d;
    --spine-rule: #8c8c8c;
    --paper-white: #ffffff;
    --photo-grey: #a7a9ac;
  }
  * { margin: 0; padding: 0; box-sizing: border-box; }
  html, body {
    width: 1200px;
    height: 846px;
    overflow: hidden;
    background: var(--ink-black);
  }
  .cover {
    position: relative;
    width: 1200px;
    height: 846px;
  }

  /* Back cover */
  .back {
    position: absolute;
    left: 0; top: 0;
    width: 564px; height: 846px;
    background: var(--ink-black);
    color: var(--paper-white);
    font-family: "Tinos", "Times New Roman", serif;
  }
  .author-photo {
    position: absolute;
    left: 198px; top: 315px;
    width: 165px; height: 165px;
    background: var(--photo-grey);
    border: 6px solid var(--paper-white);
  }
  .back-blurb {
    position: absolute;
    left: 87px; top: 492px;
    width: 386px;
    font-size: 13.7px;
    line-height: 18.3px;
    text-align: justify;
    text-align-last: justify;
  }
  .back-blurb .last-line { display: block; text-align-last: justify; }
  .publisher {
    position: absolute;
    left: 182px; top: 694px;
    width: 200px;
    text-align: center;
    font-size: 13.7px;
    line-height: 19px;
  }

  /* Spine */
  .spine {
    position: absolute;
    left: 564px; top: 0;
    width: 72px; height: 846px;
    background: var(--ink-black);
    border-left: 1.5px solid var(--spine-rule);
    border-right: 1.5px solid var(--spine-rule);
    color: var(--paper-white);
    font-family: "Tinos", "Times New Roman", serif;
    font-size: 18px;
  }
  .spine-text {
    position: absolute;
    left: 50%;
    white-space: nowrap;
    transform-origin: 0 0;
    transform: rotate(90deg) translateY(-50%);
  }
  .spine-title { top: 80px; }
  .spine-author { top: 632px; }

  /* Front cover */
  .front {
    position: absolute;
    left: 636px; top: 0;
    width: 564px; height: 846px;
    background: var(--cover-red);
    overflow: hidden;
  }
  .front-art {
    position: absolute;
    left: 240px; top: 0;
    width: 324px; height: 740px;
    background:
      radial-gradient(ellipse 55% 40% at 70% 30%, rgba(46,49,146,0.85), rgba(46,49,146,0) 70%),
      radial-gradient(ellipse 35% 30% at 90% 72%, rgba(46,49,146,0.7), rgba(46,49,146,0) 70%),
      radial-gradient(ellipse 60% 70% at 40% 50%, rgba(150,20,30,0.35), rgba(150,20,30,0) 70%);
  }
  .front-title {
    position: absolute;
    left: 50px; top: 440px;
    font-family: "Oswald", "Arial Narrow", sans-serif;
    font-weight: 700;
    font-size: 112px;
    line-height: 104px;
    letter-spacing: 2px;
    text-transform: uppercase;
  }
  .title-line {
    position: relative;
    display: block;
    color: var(--title-face);
    text-shadow:
      1px 1px 0 var(--title-edge),
      2px 2px 0 var(--title-edge),
      3px 3px 0 var(--title-edge),
      4px 4px 0 var(--title-depth),
      5px 5px 0 var(--title-depth),
      6px 6px 0 var(--title-depth),
      8px 10px 14px rgba(0,0,0,0.55);
  }
  .title-line::after {
    content: attr(data-text);
    position: absolute;
    left: 0; top: 0;
    background: linear-gradient(180deg, var(--shine-top) 0%, var(--shine-mid) 38%, var(--shine-low) 52%, #3d3d3d 78%, var(--shine-mid) 100%);
    -webkit-background-clip: text;
    background-clip: text;
    color: transparent;
    text-shadow: none;
  }
  .front-subtitle {
    position: absolute;
    left: 54px; top: 668px;
    font-family: "Montserrat", "Arial", sans-serif;
    font-weight: 500;
    font-size: 17px;
    letter-spacing: 2px;
    color: var(--sub-ink);
  }
  .front-author {
    position: absolute;
    left: 54px; top: 734px;
    font-family: "Alike", "Georgia", serif;
    font-size: 25px;
    color: var(--sub-ink);
  }
</style>
</head>
<body>
<main class="cover">

  <section class="back">
    <div class="author-photo" role="img" aria-label="Author photograph"></div>
    <p class="back-blurb">At occum aspide cuptatqui dit omnia con exerate sit ccusantorem voluptatus. Officiur autem deles voluptat inveliscid qui ides volor audi rerorit, ut doloriossus dolorem nusciatem volorio rrovitatiae. Delit ut ut ea natur res venimet apid magnat etur aut vel molore, saero te ne nonsed qui dem aut re natae cum eossimus sit is ut venis volore, ex est as si bla intio. Neque atectatus sento vit volore perum is netur, est,</p>
    <p class="publisher">Published by<br>At occum aspide</p>
  </section>

  <section class="spine">
    <span class="spine-text spine-title">Iron Ledger</span>
    <span class="spine-text spine-author">By Marcus Hale</span>
  </section>

  <section class="front">
    <div class="front-art" role="img" aria-label="Blue brush-stroke illustration with dark red streaks"></div>
    <h1 class="front-title">
      <span class="title-line" data-text="Iron">Iron</span>
      <span class="title-line" data-text="Ledger">Ledger</span>
    </h1>
    <p class="front-subtitle">She never leaves the harbor</p>
    <p class="front-author">By Marcus Hale</p>
  </section>

</main>
</body>
</html>
```